Newsletter Ad

I am looking for someone to design an advertisement for a mother's club newsletter. 4" wide X by 5" tall (and 2.5" wide X 5" tall if possible).

I'm a psychotherapist, so want the ad to look professional, but modern. I have a logo with my photo attached that can be incorporated into the design. The colors of my website are turquoise and white. I'd like to keep with that theme...so maybe some turquoise blocking to match the logo font color.

I'm uploading a logo as well as an ad draft with the content I'd like listed in the ad.

```html
<!DOCTYPE html>
<html lang="en">
<head>
<meta charset="utf-8">
<title>Dana Morrow, MA, MFT — Newsletter Ad</title>
<link rel="stylesheet" href="https://fonts.googleapis.com/css2?family=Questrial&display=swap">
<style>
  :root {
    --teal: #3a9b98;
    --teal-text: #3c9e9b;
    --bar-grey: #c1c0c0;
    --ink: #1a1a1a;
    --rule: #222222;
    --white: #ffffff;
    --portrait-light: #d9c7b8;
    --portrait-dark: #5a4a42;
  }
  * { margin: 0; padding: 0; box-sizing: border-box; }
  html, body {
    width: 1200px; height: 2400px; overflow: hidden;
    background: var(--white);
  }
  .ad {
    position: relative; width: 1200px; height: 2400px; overflow: hidden;
    background: var(--white);
    font-family: "Questrial", "Century Gothic", sans-serif;
    color: var(--ink);
  }
  .portrait {
    position: absolute; left: 373px; top: 0; width: 454px; height: 370px;
    background: linear-gradient(180deg, var(--portrait-light) 0%, #b89a85 55%, var(--portrait-dark) 100%);
  }
  .rule {
    position: absolute; left: 0; width: 1200px; height: 4px;
    background: var(--rule);
  }
  .rule--top { top: 374px; }
  .rule--bottom { top: 505px; }
  .name {
    position: absolute; left: 0; top: 378px; width: 1200px; height: 127px;
    display: flex; align-items: center; justify-content: center;
    font-size: 90px; font-weight: 400; letter-spacing: 1px;
    color: var(--teal-text); white-space: nowrap;
  }
  .name span { display: inline-block; transform: scaleY(1.28); }
  .service-title {
    position: absolute; left: 0; top: 560px; width: 1200px;
    text-align: center; font-size: 102px; line-height: 110px; padding-left: 30px;
  }
  .service-title small { font-size: 66px; }
  .audience {
    position: absolute; left: 0; top: 686px; width: 1200px;
    text-align: center; font-size: 66px; line-height: 80px;
  }
  .focus-list {
    position: absolute; left: 0; top: 813px; width: 1200px;
    list-style: none;
  }
  .focus-list li {
    height: 112px; margin-bottom: 15px;
    background: var(--bar-grey);
    display: flex; align-items: center; justify-content: center;
    font-size: 76px; white-space: nowrap;
  }
  .contact {
    position: absolute; left: 0; top: 1872px; width: 1200px; height: 368px;
    background: var(--teal); color: var(--white); font-style: normal;
    display: flex; flex-direction: column; align-items: center; justify-content: center;
    font-size: 68px; line-height: 67px; text-align: center; white-space: nowrap;
  }
  .license {
    position: absolute; right: 36px; top: 2330px;
    font-size: 54px; line-height: 60px; white-space: nowrap;
  }
</style>
</head>
<body>
  <main class="ad">
    <div class="portrait" role="img" aria-label="Portrait photo of the therapist"></div>
    <div class="rule rule--top"></div>
    <h1 class="name"><span>DANA MORROW, MA, MFT</span></h1>
    <div class="rule rule--bottom"></div>

    <p class="service-title">Psychotherapy <small>for</small></p>
    <p class="audience">Individuals, Couples and Families</p>

    <ul class="focus-list">
      <li>Parenting</li>
      <li>Depression</li>
      <li>Anxiety</li>
      <li>Life Transitions</li>
      <li>Divorce</li>
      <li>Couples Issues</li>
      <li>Women’s Issues</li>
      <li>Attachment and Neuroscience</li>
    </ul>

    <address class="contact">
      <span>148 Alder Lane, Bayview, CA 94077</span>
      <span>www.danamorrow.com</span>
      <span>dana@danamorrow.com</span>
      <span>415.555.0187</span>
    </address>

    <p class="license">License# MFC48213</p>
  </main>
</body>
</html>
```